Kestrel Facilities Business Card Design

We would now like to design business cards with the new Kestrel Facilities logo

Target Market(s)

Professional

Industry/Entity Type

Professional services

Contact Information for Business Card

Employee name, title, phone number, email address, corporate office address and logo.

Font styles to use
Sans Serif

Colors
0054AA
0677BA
7BADD7
CADEEF
E8F1F8

Requirements
Must have
• My logo
Should not have
• any other pictures or images besides my logo

```html
<!DOCTYPE html>
<html lang="en">
<head>
<meta charset="utf-8">
<title>Kestrel Facilities Business Card</title>
<link href="https://fonts.googleapis.com/css2?family=Montserrat:wght@400;500;700;800&display=swap" rel="stylesheet">
<style>
  :root {
    --stage: #2e2e30;
    --card-blue: #3375bc;
    --brand-blue: #3375bc;
    --swoosh-grey: #a7a7a9;
    --silver: #c9ccd6;
    --paper: #ffffff;
    --ink: #161616;
  }
  html, body {
    margin: 0;
    padding: 0;
    width: 1200px;
    height: 960px;
    overflow: hidden;
    background: var(--stage);
    font-family: "Montserrat", Arial, sans-serif;
  }
  .canvas {
    width: 1200px;
    height: 960px;
    display: flex;
    flex-direction: column;
    align-items: center;
    justify-content: center;
    gap: 40px;
  }
  .card {
    position: relative;
    width: 700px;
    height: 400px;
    border-radius: 22px;
    overflow: hidden;
    box-shadow: 0 10px 30px rgba(0,0,0,0.45);
  }
  /* Back side */
  .card-back {
    background: var(--card-blue);
    display: flex;
    align-items: center;
    justify-content: center;
  }
  .brand {
    display: flex;
    align-items: center;
    gap: 16px;
    font-weight: 700;
    letter-spacing: 1px;
    text-transform: uppercase;
    line-height: 1.05;
  }
  .brand-mark {
    flex: none;
    border: 6px solid currentColor;
  }
  .card-back .brand { color: var(--silver); font-size: 40px; }
  .card-back .brand-mark { width: 56px; height: 56px; }

  /* Front side */
  .card-front { background: var(--paper); }
  .card-front .wave {
    position: absolute;
    inset: 0;
    width: 700px;
    height: 400px;
  }
  .card-front .brand {
    position: absolute;
    top: 70px;
    right: 48px;
    color: var(--brand-blue);
    font-size: 32px;
  }
  .card-front .brand-mark { width: 44px; height: 44px; border-width: 5px; }
  .person {
    position: absolute;
    left: 52px;
    top: 180px;
  }
  .person-name {
    margin: 0;
    color: var(--brand-blue);
    font-weight: 800;
    font-size: 26px;
    letter-spacing: 0.5px;
  }
  .person-title {
    margin: 4px 0 0;
    color: var(--ink);
    font-weight: 500;
    font-size: 18px;
  }
  .contact {
    position: absolute;
    left: 180px;
    top: 284px;
    color: var(--paper);
    font-size: 14px;
    line-height: 1.4;
    font-weight: 400;
  }
  .contact p { margin: 0; display: flex; align-items: center; gap: 8px; }
  .contact svg { width: 13px; height: 13px; flex: none; }
</style>
</head>
<body>
<main class="canvas">
  <section class="card card-back" aria-label="Business card back">
    <div class="brand">
      <span class="brand-mark"></span>
      <span>Kestrel<br>Facilities</span>
    </div>
  </section>

  <section class="card card-front" aria-label="Business card front">
    <svg class="wave" viewBox="0 0 700 400" preserveAspectRatio="none" aria-hidden="true">
      <path fill="var(--swoosh-grey)" d="M0,318 C150,222 350,200 480,198 C580,196 640,188 690,168 C645,194 585,206 480,210 C350,214 150,232 0,338 Z"/>
      <path fill="var(--card-blue)" d="M0,400 L0,345 C150,245 350,222 480,218 C590,214 660,190 700,140 L700,400 Z"/>
    </svg>

    <div class="brand">
      <span class="brand-mark"></span>
      <span>Kestrel<br>Facilities</span>
    </div>

    <div class="person">
      <h1 class="person-name">DANA WHITFIELD</h1>
      <p class="person-title">Co-Founder</p>
    </div>

    <div class="contact">
      <p class="address">1840 N. Harbor Lane</p>
      <p class="address">Suite 204 Westvale.12</p>
      <p>
        <svg viewBox="0 0 16 16" aria-hidden="true"><path fill="#fff" d="M2 5c0-2 2-3 6-3s6 1 6 3v1h-3V5H5v1H2zM4 7h8l2 7H2z"/></svg>
        +254-700-41236
      </p>
      <p>
        <svg viewBox="0 0 16 16" aria-hidden="true"><rect x="1" y="3" width="14" height="10" fill="#fff"/><path d="M1 3l7 6 7-6" fill="none" stroke="#3375bc" stroke-width="1.3"/></svg>
        info@kestrelfac.com
      </p>
      <p>
        <svg viewBox="0 0 16 16" aria-hidden="true"><circle cx="8" cy="8" r="7" fill="#fff"/><path d="M1 8h14M8 1c-3 3-3 11 0 14M8 1c3 3 3 11 0 14" fill="none" stroke="#3375bc" stroke-width="1"/></svg>
        www.kestrelfac.com
      </p>
    </div>
  </section>
</main>
</body>
</html>
```